RWT Fittings Ltd Business Cards

We need a business card with our business logo. We provide window and door installations on high-rises in west coast British Colombia, Canada.

I would like my business information and details on one side of the card, and the other side the company name with logo

Target Market(s)

General Contractors

Industry/Entity Type

Construction

Contact Information for Business Card

one side i want my company name and logo in the dark theme logo that i provided

Requirements
Must have
• Marco Peltieri, 16045518293, RWTFittings@mailbox-demo.com, 1407-5194 Linden Row Burnaby BC, V5H 2K9, Owner & Manager

```html
<!DOCTYPE html>
<html lang="en">
<head>
<meta charset="utf-8">
<title>RWT Fittings Ltd – Business Cards</title>
<link href="https://fonts.googleapis.com/css2?family=Montserrat:wght@400;500;700&display=swap" rel="stylesheet">
<style>
  :root {
    --brand-blue: #29a8e0;
    --brand-grey: #8f8f8f;
    --ink: #1e1e1e;
    --paper: #ffffff;
    --card-dark: #111111;
    --backdrop: #e9e9ea;
  }
  * { box-sizing: border-box; margin: 0; padding: 0; }
  html, body {
    width: 1200px; height: 786px; overflow: hidden;
    background: var(--backdrop);
    font-family: "Montserrat", sans-serif;
  }
  .sheet {
    position: relative; width: 1200px; height: 786px;
    display: flex; align-items: center; justify-content: center; gap: 40px;
  }
  .card {
    position: relative; width: 540px; height: 309px;
    border-radius: 4px; overflow: hidden;
    box-shadow: 0 10px 24px rgba(0,0,0,.18);
  }
  .card--front { background: var(--paper); }
  .card--back { background: var(--card-dark); display: flex; align-items: center; justify-content: center; }

  .brand { display: flex; align-items: center; gap: 12px; }
  .brand__mark { width: 34px; height: 34px; background: var(--brand-grey); }
  .brand__name {
    font-weight: 700; color: var(--brand-blue);
    font-size: 30px; letter-spacing: .5px; white-space: nowrap;
  }
  .card--front .brand { position: absolute; left: 118px; top: 40px; }
  .card--back .brand__name { font-size: 36px; }
  .card--back .brand__mark { width: 40px; height: 40px; }

  .swoosh { position: absolute; left: 0; top: 0; width: 540px; height: 309px; }

  .person { position: absolute; left: 70px; top: 140px; text-align: right; width: 190px; }
  .person__name { color: var(--brand-blue); font-weight: 700; font-size: 21px; }
  .person__role { color: var(--ink); font-size: 12px; font-weight: 500; margin-top: 2px; }

  .divider { position: absolute; left: 276px; top: 112px; width: 1.5px; height: 80px; background: var(--brand-blue); }

  .contact { position: absolute; left: 290px; top: 112px; color: var(--ink); font-size: 11.5px; line-height: 1.3; }
  .contact__address { margin-bottom: 9px; }
  .contact__row { display: flex; align-items: center; gap: 8px; margin-bottom: 6px; }
  .contact__icon { width: 12px; height: 12px; flex: none; }
</style>
</head>
<body>
<main class="sheet">
  <section class="card card--front" aria-label="Business card front">
    <svg class="swoosh" viewBox="0 0 540 309" aria-hidden="true">
      <path d="M0 276 C 200 268, 400 244, 540 206 L540 309 L0 309 Z" fill="var(--brand-blue)"/>
      <path d="M0 268 C 200 258, 390 234, 525 204" fill="none" stroke="var(--brand-grey)" stroke-width="2.5"/>
    </svg>

    <div class="brand">
      <span class="brand__mark"></span>
      <span class="brand__name">RWT Fittings Ltd</span>
    </div>

    <div class="person">
      <p class="person__name">Marco Peltieri</p>
      <p class="person__role">Owner &amp; Manager</p>
    </div>

    <div class="divider"></div>

    <div class="contact">
      <p class="contact__address">1407-5194 Linden Row<br>Burnaby BC, V5H 2K9</p>
      <p class="contact__row">
        <svg class="contact__icon" viewBox="0 0 12 12" aria-hidden="true">
          <path d="M1 4 Q6 0 11 4 L9.5 5.5 L8 4.5 L4 4.5 L2.5 5.5 Z" fill="var(--brand-blue)"/>
          <rect x="2.5" y="6" width="7" height="5" rx="1" fill="var(--brand-blue)"/>
          <circle cx="6" cy="8.5" r="1.3" fill="var(--paper)"/>
        </svg>
        <span>16045518293</span>
      </p>
      <p class="contact__row">
        <svg class="contact__icon" viewBox="0 0 12 12" aria-hidden="true">
          <rect x="0.5" y="2.5" width="11" height="7.5" fill="var(--brand-blue)"/>
          <path d="M0.5 2.5 L6 7 L11.5 2.5" fill="none" stroke="var(--paper)" stroke-width="1"/>
        </svg>
        <span>RWTFittings@mailbox-demo.com</span>
      </p>
    </div>
  </section>

  <section class="card card--back" aria-label="Business card back">
    <div class="brand">
      <span class="brand__mark"></span>
      <span class="brand__name">RWT Fittings Ltd</span>
    </div>
  </section>
</main>
</body>
</html>
```